Moxy Fen needs some awesome stationary

Do you have what it takes to get my brand? You either do or you don't, have a crack at a design and you my just win my business.

I don't want to waste your or my time, so put your creative genius on either a business card or envelope.

I however need a package of stationary that follows the same brand. I will message you to complete the remaining should I like your first submission.

Here is what I need, have a go!

Basically I need the following for my small business based in melbourne.
- Letterhead (printer ready and MS Word)
- Business Card
- Compliments Slip
- Envelope
- Proposal Cover Page (MS Word only)
- Presentation Folder
- Marbled Fox Cards
- Student Name Tent
- Index Cards
- Vell-Ka

I am establishing the brand and it must be modern, professional but also relaxed; that is not formal and not corporate. It represents a company are leaders, but small enough to care and operate like a bunch of friends. We are bringing people and conversations back to business, and turfing out all the bureaucracy and crazy and wasteful procedures. Its about "lets talk and figure it out together and find even better ways".

Target Market(s)

Mainly companies that build software products, but Agile practices are used in many other industries (even graphic design projects)

Industry/Entity Type

Information Technology

Font styles to use
Sans Serif

Colors
3176b5
aaaaaa

Requirements
Must have
• I like curves and circles and not boxes or rectangles.
• I want a colour rich design with my brand colours, but it must be balanced.
• I want more modern than traditional, but simple modern
Should not have
• Not corporate
• Please don't waste my time if your not going to think about it.
• Don't mess with my primary logo
• Don't change my colours
• Don't overlay logo on image

```html
<!DOCTYPE html>
<html lang="en">
<head>
<meta charset="utf-8">
<title>Moxy Fen — Business Card</title>
<link rel="stylesheet" href="https://fonts.googleapis.com/css2?family=Source+Sans+3:wght@400;600;700&display=swap">
<style>
  :root {
    --brand-blue: #2c5aa1;
    --brand-grey: #959cab;
    --ink: #3b3b3b;
    --paper: #ffffff;
    --backdrop: #e8e6e2;
  }
  * { margin: 0; padding: 0; box-sizing: border-box; }
  html, body { width: 1200px; height: 987px; overflow: hidden; }
  body {
    background: var(--backdrop);
    font-family: "Source Sans 3", "Myriad Pro", Arial, sans-serif;
    position: relative;
  }
  .card {
    position: absolute;
    left: 293px;
    width: 615px;
    height: 351px;
    border-radius: 16px;
    overflow: hidden;
    box-shadow: 0 3px 10px rgba(0,0,0,0.18);
  }
  .card--front { top: 129px; background: var(--paper); }
  .card--back { top: 506px; background: var(--brand-blue); }

  /* Front: brand block */
  .brand {
    position: absolute;
    left: 40px;
    top: 62px;
    width: 236px;
    text-align: center;
  }
  .brand__dot {
    display: block;
    width: 96px;
    height: 96px;
    margin: 0 auto 16px;
    border-radius: 50%;
    background: var(--brand-blue);
  }
  .brand__name {
    font-size: 38px;
    font-weight: 700;
    color: var(--brand-blue);
    line-height: 1;
    letter-spacing: 0.3px;
  }
  .divider {
    position: absolute;
    left: 290px;
    top: 76px;
    width: 1px;
    height: 205px;
    background: #c9ccd3;
  }

  /* Front: contact */
  .contact {
    position: absolute;
    left: 319px;
    top: 72px;
    color: var(--ink);
  }
  .contact__name {
    font-size: 23px;
    font-weight: 700;
    color: var(--brand-blue);
    line-height: 1;
  }
  .contact__role {
    font-size: 16.5px;
    color: var(--brand-grey);
    margin-top: 4px;
    line-height: 1.1;
  }
  .contact__address {
    font-size: 16px;
    line-height: 22px;
    margin-top: 12px;
    font-style: normal;
  }
  .contact__list {
    list-style: none;
    margin-top: 8px;
    font-size: 16px;
    line-height: 23.5px;
  }
  .contact__list li { display: flex; align-items: center; gap: 7px; }
  .contact__list svg { width: 15px; height: 15px; fill: var(--brand-blue); flex: none; }

  /* Front: web band */
  .web-band {
    position: absolute;
    left: 0;
    top: 312px;
    width: 100%;
    height: 31px;
    background: linear-gradient(to right, var(--brand-blue) 0 457px, var(--brand-grey) 457px);
  }
  .web-band__url {
    position: absolute;
    left: 142px;
    top: 0;
    line-height: 31px;
    font-size: 16px;
    letter-spacing: 2px;
    color: #fff;
  }
  .web-band__dot {
    position: absolute;
    left: 452px;
    top: 5px;
    width: 21px;
    height: 21px;
    border-radius: 50%;
    background: #fff;
  }

  /* Back */
  .back__name {
    position: absolute;
    left: 0;
    right: 0;
    top: 130px;
    text-align: center;
    font-size: 60px;
    font-weight: 700;
    color: #fff;
    line-height: 1;
  }
  .back__url {
    position: absolute;
    left: 0;
    right: 0;
    top: 296px;
    text-align: center;
    font-size: 16px;
    letter-spacing: 3.4px;
    color: #fff;
  }
</style>
</head>
<body>
  <section class="card card--front">
    <div class="brand">
      <span class="brand__dot"></span>
      <div class="brand__name">Moxy Fen</div>
    </div>
    <div class="divider"></div>
    <div class="contact">
      <div class="contact__name">Dara Quillon</div>
      <div class="contact__role">CEO, Professional Scrum Trainer</div>
      <address class="contact__address">
        PO Box 4417<br>
        Elmsworth North<br>
        VIC 3190, Australia
      </address>
      <ul class="contact__list">
        <li><svg viewBox="0 0 16 16" aria-hidden="true"><path d="M3.6 1.2l2.2 2.9-1.3 1.6c.8 2 2.4 3.6 4.3 4.5l1.6-1.3 2.9 2.2-1.2 2.6C6.6 13.4 1.9 8.6 1 2.4z"/></svg>1300MOXYF</li>
        <li><svg viewBox="0 0 16 16" aria-hidden="true"><path d="M4.5 0.8h7v14.4h-7zM5.9 2.4v9.6h4.2V2.4z"/></svg>+61 400 127 986</li>
        <li><svg viewBox="0 0 16 16" aria-hidden="true"><path d="M1 3.5h14v9H1zM1.8 4.3L8 9l6.2-4.7z" fill-rule="evenodd"/></svg>dara@moxy-fen.com.au</li>
      </ul>
    </div>
    <div class="web-band">
      <span class="web-band__url">www.moxy-fen.com.au</span>
      <span class="web-band__dot"></span>
    </div>
  </section>

  <section class="card card--back">
    <div class="back__name">Moxy Fen</div>
    <div class="back__url">www.moxy-fen.com.au</div>
  </section>
</body>
</html>
```